Business Cards for a law firm

Business cards for our law firm. Use our silhoette logo and OAK PARTNERS - check our website (www.oakpartners.example)

Contact Information for Business Card

our silhouette logo, OAK PARTNERS, 800-555-0147, Dorian Pemberton, dorian@oakpartners.example

Requirements
Must have
• our silhouette logo, OAK PARTNERS, 800-555-0147, Dorian Pemberton, dorian@oakpartners.example

```html
<!DOCTYPE html>
<html lang="en">
<head>
<meta charset="utf-8">
<title>Oak Partners — Business Cards</title>
<link rel="stylesheet" href="https://fonts.googleapis.com/css2?family=Open+Sans:wght@400&family=Marcellus&family=Manrope:wght@400&display=swap">
<style>
  :root {
    --page: #ffffff;
    --navy: #20306a;
    --navy-soft: #24356c;
    --front-left: #000c3a;
    --front-right: #02020c;
    --card-white: #ffffff;
    --shadow: rgba(0, 0, 0, 0.45);
  }
  * { margin: 0; padding: 0; box-sizing: border-box; }
  html, body {
    width: 1200px; height: 1000px; overflow: hidden;
    background: var(--page);
  }
  .canvas { position: relative; width: 1200px; height: 1000px; }

  .card {
    position: absolute; left: 282px; width: 635px; height: 364px;
    box-shadow: 6px 8px 10px var(--shadow);
    overflow: hidden;
  }

  /* Front */
  .card-front {
    top: 111px;
    background: linear-gradient(90deg, var(--front-left) 0%, #00082a 45%, var(--front-right) 100%);
  }
  .front-band {
    position: absolute; top: -60px; height: 600px; width: 48px;
    background: rgba(0, 0, 0, 0.22);
    transform: rotate(48deg); transform-origin: top left;
  }
  .front-band.b1 { left: 190px; }
  .front-band.b2 { left: 270px; }
  .front-band.b3 { left: 390px; }
  .front-logo {
    position: absolute; left: 186px; top: 150px;
    display: flex; align-items: center; gap: 14px;
  }
  .logo-square { width: 36px; height: 36px; background: var(--navy-soft); }
  .front-logo .wordmark {
    font-family: "Open Sans", sans-serif; font-weight: 400;
    font-size: 31px; color: var(--navy-soft); letter-spacing: -0.5px;
  }

  /* Back */
  .card-back { top: 525px; background: var(--card-white); }
  .firm-line {
    position: absolute; left: 55px; top: 138px;
    display: flex; align-items: center; gap: 10px;
  }
  .firm-line .firm {
    font-family: "Open Sans", sans-serif; font-size: 18px;
    letter-spacing: 5.5px; color: var(--navy);
  }
  .firm-line .rule { width: 128px; height: 1px; background: var(--navy); }
  .person-name {
    position: absolute; left: 54px; top: 168px;
    font-family: "Marcellus", serif; font-size: 33px; font-weight: 400;
    color: var(--navy); letter-spacing: 0.2px; white-space: nowrap;
  }
  .person-contact {
    position: absolute; left: 56px; top: 213px;
    font-family: "Manrope", sans-serif; font-size: 15px; line-height: 22px;
    color: var(--navy); list-style: none;
  }
  .side-logo {
    position: absolute; left: 500px; top: 72px;
    display: flex; flex-direction: column; align-items: center; gap: 16px;
  }
  .side-logo .logo-square { width: 30px; height: 30px; background: var(--navy); }
  .side-logo .wordmark {
    writing-mode: vertical-rl;
    font-family: "Open Sans", sans-serif; font-size: 26px;
    color: var(--navy); letter-spacing: 0.5px;
  }
</style>
</head>
<body>
<main class="canvas">
  <section class="card card-front" aria-label="Card front">
    <div class="front-band b1"></div>
    <div class="front-band b2"></div>
    <div class="front-band b3"></div>
    <div class="front-logo">
      <span class="logo-square"></span>
      <span class="wordmark">OAK PARTNERS</span>
    </div>
  </section>

  <section class="card card-back" aria-label="Card back">
    <div class="firm-line">
      <span class="firm">OAK PARTNERS</span>
      <span class="rule"></span>
    </div>
    <h1 class="person-name">DORIAN PEMBERTON</h1>
    <ul class="person-contact">
      <li class="contact-email">dorian@oakpartners.example</li>
      <li class="contact-phone">800-555-0147</li>
    </ul>
    <div class="side-logo">
      <span class="logo-square"></span>
      <span class="wordmark">OAK PARTNERS</span>
    </div>
  </section>
</main>
</body>
</html>
```